Pilates business needs a face list flyer

We are a pilates business that has been based in England for 15 years and looking for a new flyer that is eye catch and modern but stylish
we are trying to capture the male market as well as the female market so the leaflet should draw attention to both groups.
I have attached a copy of the literature needed on the flyer also a picture of its founder

Target Market(s)

market age group 18-70+ male and female

Industry/Entity Type

Business

Font styles to use
Other font styles liked:
• calbri

Colors
33b8a4
34a7d8
3277b5
abd037

Requirements
Must have
• Literature attached
Nice to have
• To target both the male and female market. stylish but eye catching
Should not have
• pinks purples

```html
<!DOCTYPE html>
<html lang="en">
<head>
<meta charset="utf-8">
<title>Midland Core Pilates – Trifold Flyer</title>
<link rel="stylesheet" href="https://fonts.googleapis.com/css2?family=Open+Sans:wght@400;600;700;800&family=Carlito:wght@400;700&display=swap">
<style>
:root{
  --teal:#33b8a4;
  --sky:#34a7d8;
  --navy:#3277b5;
  --lime:#abd037;
  --ink:#4a4f55;
  --muted:#7c8389;
  --paper:#ffffff;
  --backdrop:#e9edf0;
}
*{box-sizing:border-box;margin:0;padding:0}
html,body{width:849px;height:1200px;overflow:hidden;background:var(--backdrop)}
body{font-family:"Carlito","Open Sans",sans-serif;color:var(--ink)}
.sheet{position:absolute;left:0;width:849px;background:var(--paper);overflow:hidden}
.sheet--outside{top:0;height:618px}
.sheet--inside{top:628px;height:572px}
.panel{position:absolute;top:0;height:100%;width:283px}
.panel--left{left:0}
.panel--mid{left:283px}
.panel--right{left:566px}

/* timetable */
.timetable{padding:22px 22px 0 26px}
.timetable li{list-style:none;margin-bottom:9px;font-size:9.5px;line-height:1.25}
.timetable .slot{display:block;font-weight:700;color:var(--navy)}
.timetable .slot.green{color:var(--teal)}
.timetable .venue{display:block;color:var(--muted)}

/* about */
.about{padding:20px 22px 0 18px}
.heading{font-family:"Open Sans",sans-serif;font-weight:800;text-transform:uppercase;font-size:13px;color:var(--navy);letter-spacing:.3px}
.about .founder-photo{position:absolute;top:16px;right:22px;width:68px;height:78px;background:linear-gradient(160deg,#d9d2c9,#8a7f74);border:2px solid #fff;box-shadow:0 0 0 1px #dfe3e6}
.about p{font-size:9px;line-height:1.42;color:var(--muted);margin-top:8px}
.about p.lead{padding-right:78px;margin-top:10px}
.contact{margin-top:20px;text-align:center}
.contact .call{font-family:"Open Sans",sans-serif;font-weight:800;font-size:22px;color:var(--teal);letter-spacing:.5px}
.contact .call span{font-size:14px;margin-right:6px}
.contact .line{font-size:10px;color:var(--navy);font-weight:700;margin-top:3px}

/* cover */
.cover-photo{position:absolute;left:0;top:0;width:283px;height:540px;background:linear-gradient(180deg,#f3f6f8 0%,#e2eaef 40%,#c9d7e0 75%,#aebfcb 100%)}
.cover-title{position:absolute;left:566px;top:576px;width:283px;text-align:center;font-family:"Open Sans",sans-serif;font-weight:700;font-size:12px;letter-spacing:1.5px;color:#fff;text-transform:uppercase}

.waves{position:absolute;left:0;width:849px}
.waves--outside{top:478px;height:140px}
.waves--top{top:0;height:60px}
.waves--bottom{bottom:0;height:62px}

/* inside */
.banner{position:absolute;left:283px;top:0;width:283px;height:44px;background:var(--teal);color:#fff;text-align:center;font-family:"Open Sans",sans-serif;font-weight:700;font-size:11px;letter-spacing:1.5px;line-height:44px;text-transform:uppercase}
.col{padding:68px 20px 0 24px}
.col h2{font-family:"Open Sans",sans-serif;font-weight:800;font-size:13px;color:var(--navy);text-transform:uppercase;margin-bottom:8px}
.col h3{font-family:"Open Sans",sans-serif;font-weight:700;font-size:11px;color:var(--teal);margin:11px 0 4px}
.col h3.lime{color:#8db022}
.col p{font-size:9px;line-height:1.45;color:var(--muted);margin-bottom:6px}
.col ul{list-style:none;margin-top:4px}
.col li{font-size:9px;color:var(--muted);line-height:1.55;padding-left:10px;position:relative}
.col li::before{content:"";position:absolute;left:0;top:5px;width:4px;height:4px;border-radius:50%;background:var(--teal)}
.private{margin:14px 0 8px;background:var(--teal);color:#fff;font-family:"Open Sans",sans-serif;font-weight:800;font-size:12px;text-transform:uppercase;padding:6px 10px}
.footer-web{position:absolute;left:283px;width:283px;bottom:14px;text-align:center;color:#fff;font-size:10px;font-weight:700}
</style>
</head>
<body>

<section class="sheet sheet--outside">
  <div class="panel panel--left">
    <ul class="timetable">
      <li><span class="slot">Monday 10.30am Beginner-Improver</span><span class="venue">Ashby Parish Hall, Linden Road</span></li>
      <li><span class="slot green">Monday 11.30am Small group Class</span><span class="venue">Ashby Parish Hall, Linden Road</span></li>
      <li><span class="slot">Monday 6.30pm Progressive Intermediate</span><span class="venue">Linden Community Centre, Hill St</span></li>
      <li><span class="slot">Monday 7.30pm Beginner-Improver</span><span class="venue">Linden Community Centre, Hill St</span></li>
      <li><span class="slot green">Tuesday 9.30am small group class</span><span class="venue">Elmfield Scout Hut, Mill Lane</span></li>
      <li><span class="slot">Tuesday 6.30pm Beginner-Improver</span><span class="venue">Brookside Village Hall, Church Rd</span></li>
      <li><span class="slot">Wednesday 9.30am Beginner</span><span class="venue">Ashby Parish Hall, Linden Road</span></li>
      <li><span class="slot">Wednesday 10.30am Progressive</span><span class="venue">Ashby Parish Hall, Linden Road</span></li>
      <li><span class="slot green">Wednesday 6.30pm Beginner</span><span class="venue">Elmfield Scout Hut, Mill Lane</span></li>
      <li><span class="slot">Wednesday 7.30pm Intermediate</span><span class="venue">Elmfield Scout Hut, Mill Lane</span></li>
      <li><span class="slot">Thursday 10am Beginner-Improver</span><span class="venue">Brookside Village Hall, Church Rd</span></li>
      <li><span class="slot">Thursday 6.30pm Beginner</span><span class="venue">Linden Community Centre, Hill St</span></li>
      <li><span class="slot green">Thursday 7.30pm Progressive</span><span class="venue">Linden Community Centre, Hill St</span></li>
    </ul>
  </div>

  <div class="panel panel--mid about">
    <h2 class="heading">About Clara</h2>
    <div class="founder-photo" role="img" aria-label="Portrait photo of the founder"></div>
    <p class="lead">Clara Whitfield trained as a dancer before discovering Pilates over twenty years ago and has taught full time ever since.</p>
    <p>She holds a recognised instructor diploma and continues her professional development with regular workshops, keeping her classes fresh, safe and effective for every level.</p>
    <p>Clara founded the studio fifteen years ago to bring friendly, small-group Pilates to local communities. Her classes welcome men and women of all ages, from keen athletes to those returning to exercise after injury.</p>
    <p>Every session is carefully planned so you leave feeling stronger, taller and more relaxed.</p>
    <div class="contact">
      <div class="call"><span>CALL</span>07700 900412</div>
      <div class="line">hello@midlandcorepilates.co.uk</div>
      <div class="line">www.midlandcorepilates.co.uk</div>
    </div>
  </div>

  <div class="panel panel--right">
    <div class="cover-photo" role="img" aria-label="Photo of a woman doing a Pilates stretch on a mat"></div>
  </div>

  <svg class="waves waves--outside" viewBox="0 0 849 140" preserveAspectRatio="none" aria-hidden="true">
    <path d="M283 140 C420 60 560 40 849 10 L849 140Z" fill="var(--lime)"/>
    <path d="M283 140 C440 80 600 60 849 40 L849 140Z" fill="var(--sky)"/>
    <path d="M300 140 C470 100 640 80 849 72 L849 140Z" fill="var(--teal)"/>
    <path d="M283 140 C420 112 520 110 620 118 C720 126 780 104 849 96" fill="none" stroke="#fff" stroke-width="2" opacity=".7"/>
  </svg>
  <div class="cover-title">Midland Core Pilates</div>
</section>

<section class="sheet sheet--inside">
  <svg class="waves waves--top" viewBox="0 0 849 60" preserveAspectRatio="none" aria-hidden="true">
    <path d="M0 0 L849 0 L849 30 C620 52 420 20 0 46Z" fill="var(--navy)"/>
    <path d="M0 0 L849 0 L849 18 C620 40 400 8 0 30Z" fill="var(--sky)"/>
    <path d="M0 0 L849 0 L849 6 C600 26 360 0 0 14Z" fill="var(--lime)"/>
  </svg>
  <div class="banner">Midland Core Pilates</div>

  <div class="panel panel--left col">
    <h2>What is Pilates?</h2>
    <p>Pilates is an exercise method that builds core strength, posture and body awareness through controlled, flowing movement. It suits everyone, whatever their age or fitness.</p>
    <p>Each exercise focuses on breathing, alignment and precision, working deep stabilising muscles so you move better in everyday life and in sport.</p>
    <p>Regular practice improves flexibility, balance and coordination while easing back and joint strain.</p>
    <h3>Classes</h3>
    <p>All classes are kept small so every client receives personal attention and clear guidance.</p>
    <p>Both women and men benefit from Pilates to:</p>
    <ul>
      <li>strengthen the core and back</li>
      <li>improve posture and alignment</li>
      <li>increase flexibility and mobility</li>
      <li>enhance sports performance</li>
      <li>reduce stress and tension</li>
      <li>support injury rehabilitation</li>
      <li>improve balance and coordination</li>
      <li>tone and lengthen muscles</li>
    </ul>
  </div>

  <div class="panel panel--mid col">
    <h2>Class Description</h2>
    <h3 class="lime">Small Group Pilates (New)</h3>
    <p>Our new format limits each class to six people, giving you almost one-to-one attention with the friendly feel of a group.</p>
    <p>Ideal if you want faster progress, have a specific goal, or would like extra support with technique and modifications.</p>
    <h3>Beginner Improvers</h3>
    <p>For those who have completed a beginner course or have some Pilates experience. We build on the fundamentals, adding new exercises and gentle challenges at a steady pace.</p>
    <p>Confidence, control and strength grow week by week.</p>
    <h3>Beginners</h3>
    <p>New to Pilates? Start here. We teach the key principles of breathing, alignment and core connection step by step, so you learn to move safely and correctly.</p>
    <p>No previous experience is needed and every body is welcome.</p>
  </div>

  <div class="panel panel--right col">
    <h2>Intermediate-Advanced</h2>
    <p>For experienced clients ready for a flowing, more demanding workout. Expect longer sequences, challenging variations and small equipment to test strength and stability.</p>
    <p>A great choice for runners, cyclists and anyone wanting to take their practice further.</p>
    <div class="private">Private Sessions</div>
    <p>One-to-one sessions are tailored entirely to you, whether you are recovering from injury, training for a sport or simply prefer individual coaching.</p>
    <p>Sessions can be held at home or at a local venue at a time that suits you. Please call or email for details and availability.</p>
  </div>

  <svg class="waves waves--bottom" viewBox="0 0 849 62" preserveAspectRatio="none" aria-hidden="true">
    <path d="M0 30 C260 4 520 50 849 14 L849 62 L0 62Z" fill="var(--lime)"/>
    <path d="M0 40 C280 16 540 60 849 26 L849 62 L0 62Z" fill="var(--sky)"/>
    <path d="M0 50 C300 30 560 66 849 40 L849 62 L0 62Z" fill="var(--teal)"/>
  </svg>
  <div class="footer-web">www.midlandcorepilates.co.uk</div>
</section>

</body>
</html>
```